Family business needs stationery redesign with new logo

Family owned company, established in 1987 wanting a brand 'refresh'. We are an electrical, refrigeration and construction company based in the Barkly Region Northern Territory, Australia. We have a new logo we would like to use which is uploaded along with our current letterhead and email signature. We are also dropping the word 'contractors' so please do not include this on any designs. Please note also, the 'orange' color used in our logo and designs should be Northern Territory red ochre which is as follows:

RGB (Hex): #C75B12
PantoneĀ® 159 C
CMYK: 1 / 74 / 100 / 7

We are needing our stationery redesigned using our new logo. Please include letterheads, business cards, envelopes, and email signatures.

We currently use our business letterheads for quotations, invoices, letters, HR matters, and internal memos.

We also need a separate simplified letterhead for internal paperwork such as employee leave forms, meeting agendas, and meeting minutes etc.

Reason: Needing more submissions of full package designs. We are wanting all our stationery, including business cards, letterheads, email signatures, envelopes, etc to be cohesive. We also require ALL the information, as supplied on our template letterhead, to be included on the new letterhead designs. including electrical license no.etc Thank you, R&W

Reason: needing more time as work has got in the way of looking over designs. A lot of designs not meeting the brief/criteria.

Industry/Entity Type

Business

Colors
0355a3
f37122

Requirements
Must have
• The 'orange' color used in the designs should be Northern Territory red ochre which is as follows:
• RGB (Hex): #C75B12
• PantoneĀ® 159 C
• CMYK: 1 / 74 / 100 / 7
• ***MUST INCLUDE ALL INFORMATION THAT IS ON OUR CURRENT LETTERHEAD***
Should not have
• Please do not include the word 'contractors'

```html
<!DOCTYPE html>
<html lang="en">
<head>
<meta charset="utf-8">
<title>R&amp;W Stationery Set</title>
<link href="https://fonts.googleapis.com/css2?family=Source+Sans+3:wght@400;600;700&display=swap" rel="stylesheet">
<style>
:root{
  --navy:#283270;
  --ochre:#e05f20;
  --paper:#ffffff;
  --ink:#555a63;
  --stage:#2b2b2b;
}
*{box-sizing:border-box;margin:0;padding:0}
html,body{width:1200px;height:922px;overflow:hidden;background:var(--stage);font-family:"Source Sans 3",sans-serif;color:var(--ink)}
.canvas{position:relative;width:1200px;height:922px}
.sheet{position:absolute;background:var(--paper);box-shadow:0 3px 8px rgba(0,0,0,.45);overflow:hidden}
.brand{position:absolute;font-weight:700;color:var(--navy);line-height:1;letter-spacing:.5px}
.brand-light{color:var(--paper)}
.txt{position:absolute;line-height:1.3;white-space:nowrap}
.name{font-weight:700;color:var(--navy)}
.contact-row{display:flex;align-items:center;gap:3px}
.ico{width:1em;height:1em;flex:none}
.footer-bar{position:absolute;left:0;right:0;bottom:0;height:21px;display:flex;gap:2px;background:var(--paper)}
.footer-web{background:var(--ochre);color:var(--paper);font-size:8.5px;font-weight:600;display:flex;align-items:center;padding-left:33px}
.footer-services{flex:1;background:var(--navy);color:var(--paper);font-size:8.5px;font-weight:600;display:flex;align-items:center;justify-content:flex-end;padding-right:31px}
.dot{color:var(--ochre);margin:0 2px}
.legal{font-size:7.5px}
.legal .sep{color:var(--ochre);margin:0 4px}
.divider{position:absolute;width:1px;background:var(--navy)}
.card-strip{position:absolute;bottom:0;height:4px}
</style>
</head>
<body>
<svg width="0" height="0" style="position:absolute">
  <defs>
    <symbol id="i-phone" viewBox="0 0 10 10"><path d="M2 1 L4 1 L4 3.5 L3 4.2 Q4 6.3 5.8 7 L6.5 6 L9 6 L9 8 Q9 9 8 9 Q1 8 1 2 Q1 1 2 1Z" fill="#e05f20"/></symbol>
    <symbol id="i-mobile" viewBox="0 0 10 10"><rect x="3" y="1" width="4" height="8" rx=".8" fill="none" stroke="#e05f20" stroke-width="1.2"/></symbol>
    <symbol id="i-fax" viewBox="0 0 10 10"><rect x="1" y="4" width="8" height="5" rx="1" fill="#e05f20"/><rect x="3" y="1" width="4" height="3" fill="#e05f20"/></symbol>
    <symbol id="i-mail" viewBox="0 0 10 10"><rect x="1" y="2.5" width="8" height="5" fill="#e05f20"/><path d="M1 2.5 L5 5.5 L9 2.5" fill="none" stroke="#fff" stroke-width=".8"/></symbol>
    <symbol id="i-web" viewBox="0 0 10 10"><circle cx="5" cy="5" r="4" fill="#e05f20"/></symbol>
    <symbol id="i-pin" viewBox="0 0 10 10"><path d="M5 9 L2 5 A3 3 0 1 1 8 5Z" fill="#e05f20"/></symbol>
  </defs>
</svg>

<div class="canvas">

  <section class="sheet letterhead" style="left:20px;top:190px;width:549px;height:711px">
    <div class="brand" style="left:38px;top:36px;font-size:44px">R&amp;W</div>
    <div class="txt" style="left:379px;top:35px;font-size:8.5px">PO Box 2210, 42 Marlow St<br>Redgum Flat NT 0870</div>
    <div class="txt" style="left:379px;top:63px;font-size:8.5px">
      <div class="contact-row"><svg class="ico"><use href="#i-phone"/></svg>08 8100 4321</div>
      <div class="contact-row"><svg class="ico"><use href="#i-fax"/></svg>08 8100 4399</div>
      <div class="contact-row"><svg class="ico"><use href="#i-mail"/></svg>dana@rwservices.com.au</div>
    </div>
    <div class="txt legal" style="left:85px;top:676px">ABN 12 345 678 901<span class="sep">|</span>Refrigerant Trading Authorisation AU09999<span class="sep">|</span>NT Electrical Contractors License 09876</div>
    <div class="footer-bar">
      <div class="footer-web" style="width:150px">www.rwservices.com.au</div>
      <div class="footer-services">Electrical<span class="dot">•</span>Refrigeration<span class="dot">•</span>Building Services</div>
    </div>
  </section>

  <section class="sheet card-wide" style="left:606px;top:22px;width:359px;height:140px">
    <div class="brand" style="left:18px;top:16px;font-size:22px">R&amp;W</div>
    <div class="txt" style="left:16px;top:57px;font-size:10px"><span class="name">Dana Merrick</span></div>
    <div class="txt" style="left:16px;top:70px;font-size:6.5px">Corporate Services Manager, R&amp;W</div>
    <div class="txt" style="left:16px;top:87px;font-size:6.3px">
      <div class="contact-row"><svg class="ico"><use href="#i-phone"/></svg>08 8100 4321</div>
      <div class="contact-row"><svg class="ico"><use href="#i-mobile"/></svg>0400 123 987</div>
      <div class="contact-row"><svg class="ico"><use href="#i-fax"/></svg>08 8100 4399</div>
      <div class="contact-row"><svg class="ico"><use href="#i-mail"/></svg>dana@rwservices.com.au</div>
      <div class="contact-row"><svg class="ico"><use href="#i-web"/></svg>www.rwservices.com.au</div>
    </div>
    <div class="txt" style="left:145px;top:112px;font-size:6.3px">
      <div class="contact-row"><svg class="ico"><use href="#i-pin"/></svg>PO Box 2210, 42 Marlow St</div>
      <div style="padding-left:9px">Redgum Flat NT 0870</div>
    </div>
  </section>

  <section class="sheet card-front" style="left:606px;top:190px;width:227px;height:129px;border-radius:5px">
    <div class="brand" style="left:18px;top:59px;font-size:22px">R&amp;W</div>
    <div class="divider" style="left:87px;top:26px;height:72px"></div>
    <div class="txt" style="left:97px;top:24px;font-size:9px"><span class="name">Dana Merrick</span></div>
    <div class="txt" style="left:97px;top:35px;font-size:5.5px">Corporate Services Manager, R&amp;W</div>
    <div class="txt" style="left:97px;top:47px;font-size:5.5px">PO Box 2210, 42 Marlow St<br>Redgum Flat NT 0870</div>
    <div class="txt" style="left:97px;top:67px;font-size:5.5px">
      <div class="contact-row"><svg class="ico"><use href="#i-phone"/></svg>08 8100 4321</div>
      <div class="contact-row"><svg class="ico"><use href="#i-mobile"/></svg>0400 123 987</div>
      <div class="contact-row"><svg class="ico"><use href="#i-fax"/></svg>08 8100 4399</div>
      <div class="contact-row"><svg class="ico"><use href="#i-mail"/></svg>dana@rwservices.com.au</div>
      <div class="contact-row"><svg class="ico"><use href="#i-web"/></svg>www.rwservices.com.au</div>
    </div>
    <div class="card-strip" style="left:0;width:87px;background:var(--ochre)"></div>
    <div class="card-strip" style="left:88px;right:0;background:var(--navy)"></div>
  </section>

  <section class="sheet card-back" style="left:846px;top:190px;width:227px;height:129px;border-radius:5px;background:var(--ochre)">
    <div class="brand brand-light" style="left:0;right:0;top:46px;text-align:center;font-size:30px">R&amp;W</div>
    <div class="txt" style="left:0;right:0;top:110px;text-align:center;color:var(--paper);font-size:5.8px;font-weight:600">Electrical • Refrigeration • Building Services</div>
  </section>

  <section class="sheet envelope-back" style="left:607px;top:366px;width:574px;height:250px">
    <svg style="position:absolute;left:0;top:0" width="574" height="76" viewBox="0 0 574 76" aria-hidden="true">
      <path d="M0 0 H574 L564 62 Q562 72 550 72 H24 Q12 72 9 62 Z" fill="#e05f20"/>
    </svg>
    <div class="brand brand-light" style="left:0;right:0;top:26px;text-align:center;font-size:22px">R&amp;W</div>
  </section>

  <section class="sheet envelope-front" style="left:606px;top:650px;width:574px;height:252px">
    <div class="brand" style="left:26px;top:22px;font-size:38px">R&amp;W</div>
    <div class="txt" style="left:25px;top:83px;font-size:8.5px">PO Box 2210, 42 Marlow St<br>Redgum Flat NT 0870</div>
    <div class="footer-bar">
      <div class="footer-web" style="width:144px;padding-left:24px">www.rwservices.com.au</div>
      <div class="footer-services">Electrical<span class="dot">•</span>Refrigeration<span class="dot">•</span>Building Services</div>
    </div>
  </section>

</div>
</body>
</html>
```